Business card design Needed for new logo / Construction business, home extensions and new builds

We need a business card design using our new logo files which i will attach to this project :)

We are a small construction business specialising in home extensions, new builds and property development. We are very ambitious and would appreciate professional and elegant designs for our new business card.

Very serious about using the services on MakerQuarry and recently acquired our new logo from here :)

Please get involved, i will feedback when i can as i am very busy but can respond daily, thanks

Target Market(s)

People that want to build onto their houses, new building developments or adding too their existing property

Industry/Entity Type

Construction

Contact Information for Business Card

Renwick Tolliver Construction, Lionel Ashby (Managing Director), Tel 07822254961, email - info@renwick-tolliver, www.renwick-tolliver.co.uk

Colors

Designer to choose colors to be used in the design.

Requirements
Must have
• I like a deep grey on the back please. A lot of you have provided black from and back, try mixing things up a little. The black looks cool 😎 Thanks

```html
<!DOCTYPE html>
<html lang="en">
<head>
<meta charset="utf-8">
<title>Renwick Tolliver Construction – Business Card</title>
<link rel="stylesheet" href="https://fonts.googleapis.com/css2?family=Open+Sans:wght@400;600;700&display=swap">
<style>
  :root {
    --backdrop: #2a2a2d;
    --card-black: #1e1d21;
    --card-grey: #6e6f71;
    --grey-ink: #58595b;
    --gold: #d4a53a;
    --gold-light: #f1d27a;
    --gold-dark: #9c7420;
    --silver: #d9d9db;
    --white: #f2f2f2;
  }
  * { box-sizing: border-box; margin: 0; padding: 0; }
  html, body {
    width: 1200px; height: 780px; overflow: hidden;
    background: var(--backdrop);
    font-family: "Open Sans", sans-serif;
  }
  .canvas {
    position: relative; width: 1200px; height: 780px;
    display: flex; align-items: center; justify-content: center; gap: 60px;
  }
  .card {
    position: relative; width: 520px; height: 298px;
    border-radius: 3px; overflow: hidden;
    box-shadow: 0 10px 30px rgba(0,0,0,.35);
  }
  .card--front { background: var(--card-black); color: var(--white); }
  .card--back { background: var(--card-grey); display: flex; align-items: center; justify-content: center; }

  .brand { position: absolute; top: 28px; left: 32px; display: flex; align-items: center; gap: 10px; }
  .brand__mark { width: 14px; height: 14px; background: var(--gold); }
  .brand__name {
    font-size: 15px; font-weight: 600; letter-spacing: 1.5px;
    text-transform: uppercase; color: var(--gold); line-height: 1.25;
  }

  .address { position: absolute; top: 92px; left: 32px; font-size: 13px; line-height: 1.5; color: var(--white); }

  .contacts { position: absolute; left: 32px; bottom: 34px; list-style: none; font-size: 12.5px; line-height: 1.75; }
  .contacts li { display: flex; align-items: center; gap: 8px; }
  .contacts svg { width: 12px; height: 12px; flex: none; }

  .person { position: absolute; right: 78px; bottom: 56px; text-align: right; }
  .person__name { font-size: 28px; font-weight: 700; line-height: 1.1; }
  .person__first { color: var(--silver); }
  .person__last { color: var(--gold); }
  .person__title { font-size: 14px; color: var(--white); margin-top: 4px; }

  .gold-steps { position: absolute; right: 0; bottom: 34px; width: 62px; }
  .gold-steps span {
    display: block; height: 10px; margin-bottom: 3px;
    background: linear-gradient(180deg, var(--gold-light), var(--gold) 55%, var(--gold-dark));
  }
  .gold-steps span:nth-child(2) { margin-left: 8px; }
  .gold-steps span:nth-child(3) { margin-left: 16px; }
  .gold-steps span:nth-child(4) { margin-left: 24px; }

  .back-brand { display: flex; align-items: center; gap: 14px; }
  .back-brand__mark { width: 22px; height: 22px; background: var(--grey-ink); }
  .back-brand__name {
    font-size: 22px; font-weight: 600; letter-spacing: 2px;
    text-transform: uppercase; color: var(--grey-ink); line-height: 1.25;
  }
</style>
</head>
<body>
<main class="canvas">
  <section class="card card--front" aria-label="Business card front">
    <div class="brand">
      <span class="brand__mark"></span>
      <span class="brand__name">Renwick Tolliver<br>Construction</span>
    </div>
    <p class="address">Harlow Lane, Westbury<br>Oakminster, OK4 7RT</p>
    <ul class="contacts">
      <li>
        <svg viewBox="0 0 12 12" aria-hidden="true"><path d="M3 1l2 2.5-1.2 1.2a7 7 0 003.5 3.5L8.5 7 11 9l-1.3 2C5 11 1 7 1 2.3z" fill="var(--gold)"/></svg>
        07822254961
      </li>
      <li>
        <svg viewBox="0 0 12 12" aria-hidden="true"><circle cx="6" cy="6" r="5" fill="none" stroke="var(--gold)" stroke-width="1.3"/><path d="M1 6h10M6 1c-2.5 3-2.5 7 0 10M6 1c2.5 3 2.5 7 0 10" fill="none" stroke="var(--gold)" stroke-width="1"/></svg>
        info@renwick-tolliver.co.uk
      </li>
      <li>
        <svg viewBox="0 0 12 12" aria-hidden="true"><rect x="1" y="2.5" width="10" height="7" fill="none" stroke="var(--gold)" stroke-width="1.3"/><path d="M1 2.5l5 4 5-4" fill="none" stroke="var(--gold)" stroke-width="1.2"/></svg>
        www.renwick-tolliver.co.uk
      </li>
    </ul>
    <div class="person">
      <p class="person__name"><span class="person__first">Lionel</span> <span class="person__last">Ashby</span></p>
      <p class="person__title">Managing Director</p>
    </div>
    <div class="gold-steps" aria-hidden="true"><span></span><span></span><span></span><span></span></div>
  </section>

  <section class="card card--back" aria-label="Business card back">
    <div class="back-brand">
      <span class="back-brand__mark"></span>
      <span class="back-brand__name">Renwick Tolliver<br>Construction</span>
    </div>
  </section>
</main>
</body>
</html>
```